Companybrochure for Consulting & Financing Firm

I need to have a Company Brochure asap for our company. We have a website that describes what we do, but we need also a brochure, that can be sent by PDF of eventually be printed as well.

The brochure should be short but nice and appealing to the customers.

We provide professional management consulting and help our customers to get finance for very diferent projects. Our business has a lot to do with personal relations, but also we are very professional in the way we work and how develop the solutions for our clients. Our clients are mainly government-owned firm, but also private trading companies and wealthy private investors.

Our customers are mainly in Latin America, but the company is headquater is in Switzerland. We are opening offices in Panama and Caracas, this should be easaly be adabtable later.

Please have a look at our website www.vorelpartners.ch. In the brochure, we would segment our services in 1.) Project Developments 2.) Management Conulting 3.) Investment Management and 4.) Finance Solutions.

Also do have a look at www.vorelpartners.ch
(Click E for the English version)
Updates

I managed to put the Mock-Up to the Website.
It is actually not really a mock-up, it is a version I have designed myself.
Well as I am not a designer, I hope you can make it much better.
The content however is what I would put in any other design as well.

Target Market(s)

Top Management, Investors, Entrepreneurs, Government Officials

Industry/Entity Type

Management Consulting

Requirements
Must have
• Design should reflect this image elements:

We are entrepreneurs.
We are comitted to get things done.
We work closely with the client side by side.
We are a professional partner.
We are not afraid of delivering unconventional solutions.
We look at the problem from various angles.
We analyse, develop solutions and implent results.
Should not have
• Typical US-American style elements. We do not want to give the impression of being a US company.

We do not want to appear to be neo-liberal. We are a politically neutral professional consulting firm.

```html
<!DOCTYPE html>
<html lang="en">
<head>
<meta charset="utf-8">
<title>Company Brochure – Spread 1–2</title>
<link rel="stylesheet" href="https://fonts.googleapis.com/css2?family=Open+Sans:wght@400;600;700&display=swap">
<style>
  :root {
    --backdrop: #e8e6e2;
    --paper: #ffffff;
    --paper-shade: #dcdde0;
    --blue-bar: #2d5f9e;
    --blue-panel-top: #4a97d2;
    --blue-panel-bottom: #2f78b7;
    --text-light: #eef5fc;
    --rule-blue: #2a63a6;
  }
  * { box-sizing: border-box; margin: 0; padding: 0; }
  html, body { width: 1200px; height: 900px; overflow: hidden; }
  body {
    background: var(--backdrop);
    font-family: "Open Sans", Arial, sans-serif;
    position: relative;
  }
  .spread {
    position: absolute;
    left: 60px; top: 170px;
    width: 1080px; height: 560px;
    display: flex;
    box-shadow: 0 10px 30px rgba(0,0,0,0.18);
  }
  .page {
    position: relative;
    width: 540px; height: 560px;
    background: var(--paper);
    overflow: hidden;
  }
  .page--left { background: linear-gradient(to right, var(--paper) 85%, var(--paper-shade)); }
  .page--right { background: linear-gradient(to left, var(--paper) 85%, var(--paper-shade)); }

  .photo {
    position: absolute;
    border-radius: 18px;
  }
  .photo--media-wall {
    left: 30px; top: 40px; width: 340px; height: 320px;
    background: linear-gradient(120deg, #3d6fa3 0%, #8fb86a 35%, #e0b04a 55%, #c9d3dc 80%, #eef1f4 100%);
  }
  .photo--seedling {
    left: 30px; top: 30px; width: 370px; height: 290px;
    background: radial-gradient(ellipse at 55% 45%, #5f7a3a 0%, #3a3330 30%, #1b1b1d 70%);
  }

  .info-panel {
    position: absolute;
    border-radius: 0 0 16px 16px;
    background: linear-gradient(to bottom, var(--blue-panel-top), var(--blue-panel-bottom));
    color: var(--text-light);
    padding-bottom: 18px;
  }
  .info-panel__title {
    background: var(--blue-bar);
    color: #fff;
    font-weight: 700;
    font-size: 15px;
    line-height: 1.4;
    padding: 6px 12px;
    border-radius: 10px 10px 0 0;
    white-space: nowrap;
  }
  .info-panel__body { padding: 12px 16px 0; font-size: 12px; line-height: 1.45; }
  .info-panel__body p + p { margin-top: 10px; }
  .service-list { list-style: none; margin-top: 12px; }
  .service-list li { margin-top: 2px; }
  .service-list li::before { content: ">"; font-weight: 700; margin-right: 10px; }

  .info-panel--intro { left: 200px; top: 245px; width: 320px; }
  .info-panel--project { left: 195px; top: 250px; width: 325px; }

  .page-rule { position: absolute; left: 0; top: 0; width: 540px; height: 560px; }
  .page-number {
    position: absolute;
    width: 30px; height: 26px;
    background: var(--rule-blue);
    color: #fff;
    font-weight: 700;
    font-size: 13px;
    display: flex; align-items: center; justify-content: center;
  }
  .page-number--left { left: 0; bottom: 22px; }
  .page-number--right { right: 0; bottom: 60px; }
</style>
</head>
<body>
  <main class="spread">
    <section class="page page--left">
      <div class="photo photo--media-wall" role="img" aria-label="Hand reaching toward a wall of colourful media thumbnails"></div>
      <div class="info-panel info-panel--intro">
        <h2 class="info-panel__title">&gt; Analyze &gt;&gt; Develop &gt;&gt;&gt; Deliver</h2>
        <div class="info-panel__body">
          <p>We are a professional consulting, financing and investment firm operating in the fields of:</p>
          <ul class="service-list">
            <li>Project Development</li>
            <li>Management Consulting</li>
            <li>Investment Management</li>
            <li>Finance Solutions</li>
          </ul>
        </div>
      </div>
      <svg class="page-rule" viewBox="0 0 540 560" aria-hidden="true">
        <path d="M30 528 Q 280 520 540 470" fill="none" stroke="#2a63a6" stroke-width="2"/>
      </svg>
      <div class="page-number page-number--left">1</div>
    </section>

    <section class="page page--right">
      <div class="photo photo--seedling" role="img" aria-label="Cupped hands holding soil with a young green seedling"></div>
      <div class="info-panel info-panel--project">
        <h2 class="info-panel__title">&gt;&gt; Project Development</h2>
        <div class="info-panel__body">
          <p>Sometimes a project with high potential has to be developed before its economic value becomes apparent.</p>
          <p>In such situations, we participate financially in the project and commit ourselves as entrepreneurs together with the owners.</p>
          <p>We also take care of project management.</p>
        </div>
      </div>
      <svg class="page-rule" viewBox="0 0 540 560" aria-hidden="true">
        <path d="M0 470 Q 260 488 510 487" fill="none" stroke="#2a63a6" stroke-width="2"/>
      </svg>
      <div class="page-number page-number--right">2</div>
    </section>
  </main>
</body>
</html>
```